BRIGHT RIVER POWER.

I'd like my business logo.
contact name: Dennis Halvorsen
phone:0438759164
email: info@brightriverpower.net.au
website: www.brightriverpower.net.au

services:
solar
battery storage
LED lighting
energy saving solutions
general electrical
I'd like the design to look professional

Target Market(s)

Everyone

Industry/Entity Type

Business

Contact Information for Business Card

as described above

Requirements
Must have
• Id like the colours and the design to work well with my logo.

```html
<!DOCTYPE html>
<html lang="en">
<head>
<meta charset="utf-8">
<title>Bright River Power – Business Card</title>
<link rel="stylesheet" href="https://fonts.googleapis.com/css2?family=Open+Sans:wght@400;600;700&display=swap">
<style>
  :root {
    --canvas-bg: #ededed;
    --card-white: #ffffff;
    --brand-green: #4aa538;
    --green-light: #8dc63f;
    --green-dark: #3f9a35;
    --sun-orange: #f6a31b;
    --text-grey: #4a4a4a;
    --white: #ffffff;
  }
  * { box-sizing: border-box; margin: 0; padding: 0; }
  html, body {
    width: 1105px;
    height: 1200px;
    overflow: hidden;
    background: var(--canvas-bg);
    font-family: "Open Sans", Arial, sans-serif;
  }
  .canvas {
    position: relative;
    width: 1105px;
    height: 1200px;
  }
  .card {
    position: absolute;
    left: 192px;
    width: 720px;
    height: 410px;
  }
  .card-front {
    top: 130px;
    background: var(--card-white);
  }
  .card-back {
    top: 660px;
    background: radial-gradient(ellipse at 50% 48%, var(--green-light) 0%, var(--brand-green) 62%, var(--green-dark) 100%);
  }

  /* Brand name lockup */
  .brand {
    position: absolute;
    display: flex;
    align-items: center;
    gap: 14px;
  }
  .brand-mark {
    width: 58px;
    height: 58px;
    border-radius: 50%;
    flex: none;
  }
  .brand-name {
    font-weight: 700;
    line-height: 1.05;
    letter-spacing: 0.5px;
  }
  .card-front .brand {
    right: 48px;
    top: 64px;
  }
  .card-front .brand-mark { background: var(--sun-orange); }
  .card-front .brand-name {
    color: var(--brand-green);
    font-size: 30px;
  }

  .card-back .brand {
    left: 50%;
    top: 120px;
    transform: translateX(-50%);
    white-space: nowrap;
  }
  .card-back .brand-mark {
    width: 84px;
    height: 84px;
    background: var(--white);
  }
  .card-back .brand-name {
    color: var(--white);
    font-size: 44px;
  }

  /* Contact block */
  .contact-name {
    position: absolute;
    left: 46px;
    top: 232px;
    font-size: 25px;
    font-weight: 600;
    color: var(--brand-green);
  }
  .contact-list {
    position: absolute;
    left: 46px;
    top: 286px;
    list-style: none;
  }
  .contact-item {
    display: flex;
    align-items: center;
    gap: 10px;
    height: 28px;
    font-size: 18px;
    color: var(--text-grey);
  }
  .contact-icon {
    width: 17px;
    height: 17px;
    flex: none;
    fill: var(--brand-green);
  }

  /* Services */
  .services {
    position: absolute;
    left: 0;
    right: 0;
    top: 316px;
    text-align: center;
    color: var(--white);
    font-size: 19px;
    line-height: 28px;
  }
  .services .dot {
    display: inline-block;
    width: 7px;
    height: 7px;
    border-radius: 50%;
    background: var(--white);
    margin: 0 8px;
    vertical-align: middle;
  }
</style>
</head>
<body>
<main class="canvas">

  <section class="card card-front">
    <div class="brand">
      <span class="brand-mark"></span>
      <span class="brand-name">Bright River<br>Power</span>
    </div>

    <h1 class="contact-name">Dennis Halvorsen</h1>
    <ul class="contact-list">
      <li class="contact-item">
        <svg class="contact-icon" viewBox="0 0 24 24" aria-hidden="true"><path d="M6.6 10.8a15.1 15.1 0 0 0 6.6 6.6l2.2-2.2c.3-.3.7-.4 1-.2 1.1.4 2.3.6 3.6.6.6 0 1 .4 1 1V20c0 .6-.4 1-1 1A17 17 0 0 1 3 4c0-.6.4-1 1-1h3.5c.6 0 1 .4 1 1 0 1.2.2 2.4.6 3.6.1.3 0 .7-.2 1z"/></svg>
        <span>0438759164</span>
      </li>
      <li class="contact-item">
        <svg class="contact-icon" viewBox="0 0 24 24" aria-hidden="true"><path d="M2 5h20v14H2z" fill="none"/><path d="M2 6v12h20V6l-10 7z"/><path d="M2.5 5h19L12 11.6z"/></svg>
        <span>info@brightriverpower.net.au</span>
      </li>
      <li class="contact-item">
        <svg class="contact-icon" viewBox="0 0 24 24" aria-hidden="true"><circle cx="12" cy="12" r="10"/><path d="M2 12h20M12 2c3 3 3 17 0 20M12 2c-3 3-3 17 0 20" stroke="#fff" stroke-width="1.4" fill="none"/></svg>
        <span>www.brightriverpower.net.au</span>
      </li>
    </ul>
  </section>

  <section class="card card-back">
    <div class="brand">
      <span class="brand-mark"></span>
      <span class="brand-name">Bright River Power</span>
    </div>
    <p class="services">
      Solar<span class="dot"></span>Battery storage<span class="dot"></span>LED lighting<br>
      Energy saving solutions
    </p>
  </section>

</main>
</body>
</html>
```